TalkSift Website Re-skin

TalkSift.com needs to be re-skinned. The form design of the website and talksift logo are is to stay as-is. The images, type font and background color need to be updated to attempt to achieve a professionally-progressive first impression. We are also amiable to any recommended copy changes, but the main focus of this initiative is to replace the tired and muted existing images, background, and type font. I have included a number of websites that have the look and feel that we would like to inspire the refresh.... These websites also do a good job to include images that blend a computer, ipad, or iphone with a somewhat blurred background.

I included two company overview documents to describe the service. You can also log into the site and receive 5 Free interviews so that you can experience the site yourself in about 10 minutes.

Another high level overview is described in this video link:
http://clipmarsh.example/q7Lr2-Xpdwe
Updates

We received some questions from a few designers and I want to make sure that I share my responses with everyone.  

How many pages do we want:  
We would like 3 pages.  The Home Page, the Login Page, and the Create Account Page.  Note: The large majority of the work should be focused on the Home Page.  The Login and Create Account pages just need to have the background and overall theme from the Home Page design.  

Is coding a must for the Project:  
Coding is highly preferred as it will help reduce the process of splicing up the artwork files.  As such, our preference is to obtain the coding with the project. 

What type of Coding do we want?
HTML/CSS is acceptable

Note:  I also added some Logo .png files onto the craft yard site

Target Market(s)

Please refer to the attached "company description" and "business overview" documents. General target audience is small, medium and large organizations seeking to reduce the time and cost to interview qualified job candidates. Given that TalkSift serves small to large organizations, we would like our design to error on the size of "professionally progressive" such that it has the visual appearance of being sophisticated and technologically sound.

Industry/Entity Type

Computer

Requirements
Must have
• Seeking to have 3 pages re-skinned. The Home Page, the Login Page, and the Create Account Page. Note. The Login and Create Account Pages should be very straight forward with limited work required as we seek little design change for them and would like them to carry over the theme and colors from the Home Page. Hence, re-skinning the home page with the elements described below is the major focus.

Top of Home Page: Replace main image of lady coming out of resume/ipad screen with an image very similar to the one on the attached file titled "plinko home page lady" Note: Plinko changed its name to Brisel so duplicating this approach is okay to mimic this image without issue. We especially like this image as it is colorful and visually describes the service we provide.

The layout of the "Oru iPad" and "Telvo Home page i-pad" files that are attached are nice. There may be a way to leverage the plinko lady with the Oru Ipad image to make a nice visual.

Verbiage: Change copy from "Welcome to Talksift! Talksift is your fully automated interviewing solution. Personalized to your brand, you will save time and money selecting the best candidates" To Now Read: "Humanize and accelerate your interview screening process with TalkSift."

Background: We really like the way that Oru changes their back-grounds as the themes/subjects change when scrolling down their main web page. Achieving this sort of experience would be ideal. It is also acceptable to have a more contrasting background color that may be darker. If this is done, then the words could be in white. This is not a requirement, just some general direction.

Font type: We like the font type from Oru (see attached file titled "Oru iPad")

Font Color: Okay to change font from the dull blue that we have today and use a different more contrasting or popping color.

We like outlining steps 1 through 4 but prefer to replace the people holding the placards with some other images that are potentially in a family of images that all tie together.

It is okay to keep the images in the "Responsive Layout" section of the site (located about 3/4ths of the way down the page) as these seem to be more current and do a good job to illustrate images with an ipad or computer.

Benefits Section: Prefer to change this section. Listing nine (9) separate benefits are too many to make any impact. Advocate illustrating the following benefits:
- "Reduce time and cost to screen candidates"
- "Design site with your logo and colors"
- "Customize interview questions for all your postings"
- "Interview candidates anywhere in the world"
- "Review candidate video's anytime / anywhere"

Nice to have
• Potential to add an image whereby it shows / illustrates talksift's administrative portal "talksift admin portal" (attached) to an image of an ipad screen similar to how the attached images for the following websites: "Telvo" "WeareHalcyon" and "marshbell"

```html
<!DOCTYPE html>
<html lang="en">
<head>
<meta charset="utf-8">
<title>TalkSift – Bring Resumes to Life</title>
<link rel="stylesheet" href="https://fonts.googleapis.com/css2?family=Varela+Round&family=Open+Sans:wght@400;600&display=swap">
<style>
  :root{
    --blue-deep:#0d6fae;
    --blue-mid:#1f8fd0;
    --blue-light:#5fb6e6;
    --blue-text:#1a7dc0;
    --blue-link:#2c86c7;
    --orange:#e0a11b;
    --ink:#2b2b2b;
    --grey:#7a7a7a;
    --grey-light:#9a9a9a;
    --rule:#dedede;
    --panel:#f7f7f7;
    --white:#ffffff;
  }
  *{box-sizing:border-box;margin:0;padding:0}
  html,body{width:1200px;height:2206px;overflow:hidden}
  body{position:relative;background:var(--white);font-family:"Open Sans",Arial,sans-serif;color:var(--ink)}
  .abs{position:absolute}

  /* header */
  .site-header{left:0;top:0;width:1200px;height:106px;background:linear-gradient(180deg,#1d8fd2 0%,#0f74b6 100%)}
  .brand{left:91px;top:18px;display:flex;align-items:center;gap:10px}
  .brand-mark{width:66px;height:66px;border-radius:50%;background:#e8f4fc}
  .brand-name{font-family:"Varela Round",Arial,sans-serif;color:var(--white);font-size:27px;letter-spacing:2px;line-height:1}
  .brand-tag{font-family:"Varela Round",Arial,sans-serif;color:var(--white);font-size:12px;letter-spacing:1.5px;margin-top:4px}
  .main-nav{top:44px;font-family:"Open Sans",Arial,sans-serif;font-size:19px;color:var(--white)}

  /* hero */
  .hero{left:0;top:106px;width:1200px;height:470px;background:radial-gradient(ellipse at 70% 40%,#6cc2ee 0%,#2b98d6 45%,#0e6fb0 100%)}
  .hero-kicker{left:99px;top:204px;font-family:"Varela Round",Arial,sans-serif;font-size:34px;color:var(--white)}
  .hero-title{left:99px;top:244px;font-family:"Varela Round",Arial,sans-serif;font-size:47px;color:var(--white)}
  .hero-copy{left:99px;top:304px;font-size:14.5px;line-height:25px;color:#cfe8f8}
  .btn-read{left:99px;top:368px;width:123px;height:35px;background:linear-gradient(180deg,#1b79b8,#0d5a90);border:1px solid #0a4d7d;border-radius:3px;color:var(--white);font-size:13px;font-weight:600;text-align:center;line-height:33px}
  .slider-dots{left:99px;top:429px;display:flex;gap:6px}
  .slider-dots span{width:12px;height:12px;border-radius:50%;background:#8ec8ea}
  .slider-dots span.on{background:var(--white)}
  .hero-visual{left:596px;top:132px;width:507px;height:361px;border-radius:18px;background:linear-gradient(135deg,#f2f4f6 0%,#c9d3da 30%,#7fb6da 55%,#3d4a55 75%,#d8e2ea 100%)}

  /* welcome */
  .welcome-title{left:0;top:620px;width:1200px;text-align:center;font-family:"Varela Round",Arial,sans-serif;font-size:32px;color:var(--ink)}
  .welcome-lead{left:0;top:673px;width:1200px;text-align:center;font-size:17px;color:var(--grey)}
  .welcome-copy{left:120px;top:700px;width:960px;text-align:center;font-size:13.5px;line-height:25px;color:var(--grey-light)}

  /* steps */
  .steps{left:0;top:801px;width:1200px;height:500px;background:linear-gradient(180deg,#eef0f0 0%,#e4e2dc 45%,#cfcac0 75%,#e9e9e6 100%)}
  .steps-title{left:0;top:850px;width:1200px;text-align:center;font-family:"Varela Round",Arial,sans-serif;font-size:35px;color:var(--blue-text)}
  .steps-sub{left:0;top:898px;width:1200px;text-align:center;font-family:"Varela Round",Arial,sans-serif;font-size:28px;color:var(--blue-text)}
  .step-card{top:963px;width:247px;height:280px;background:rgba(255,255,255,.86);border:1px solid #e2e2e2;border-radius:10px;box-shadow:0 2px 6px rgba(0,0,0,.08)}
  .step-icon{position:absolute;left:50%;top:26px;transform:translateX(-50%)}
  .step-head{position:absolute;left:0;top:128px;width:100%;display:flex;justify-content:center;align-items:center;gap:8px;font-family:"Varela Round",Arial,sans-serif;font-size:24px;color:var(--blue-text)}
  .step-num{width:34px;height:34px;border-radius:50%;background:var(--blue-link);color:var(--white);font-size:19px;text-align:center;line-height:34px;flex:none}
  .step-head.two-line{top:118px;line-height:28px}
  .step-head.two-line span.lbl{text-align:center}
  .step-copy{position:absolute;left:20px;top:180px;width:207px;text-align:center;font-size:13px;line-height:22px;color:var(--grey)}

  /* admin portal */
  .portal{left:0;top:1301px;width:1200px;height:409px;background:var(--panel);border-bottom:1px solid #d5d5d5}
  .portal-title{left:85px;top:1388px;font-family:"Varela Round",Arial,sans-serif;font-size:32px;color:var(--ink)}
  .portal-copy{left:87px;top:1437px;width:415px;font-size:12.5px;line-height:24.5px;color:var(--grey)}
  .portal-copy p+p{margin-top:10px}
  .tablet-frame{left:543px;top:1356px;width:572px;height:354px;background:#eeeeee;border:1px solid #d8d8d8;border-bottom:none;border-radius:22px 22px 0 0}
  .tablet-home{left:1073px;top:1513px;width:30px;height:30px;border-radius:50%;background:#f7f7f7;border:1px solid #d8d8d8}
  .tablet-screen{left:596px;top:1404px;width:466px;height:306px;background:linear-gradient(180deg,#ffffff 0%,#f1f1f1 100%);border:1px solid #cfcfcf}

  /* pricing */
  .pricing-title{left:82px;top:1772px;font-family:"Varela Round",Arial,sans-serif;font-size:29px;color:var(--blue-text)}
  .price-table{left:85px;top:1820px;width:586px;border-collapse:collapse;font-size:16px}
  .price-table td{height:60px;color:var(--ink);border-bottom:1px solid var(--rule)}
  .price-table tr:last-child td{border-bottom:none;padding-top:12px}
  .price-table td.lbl{color:var(--blue-link);width:216px}
  .price-table td.num{width:100px}
  .btn-try{left:85px;top:1997px;width:105px;height:32px;background:linear-gradient(180deg,#3a8fca,#1f6ea8);border:1px solid #1a5e90;border-radius:3px;color:var(--white);font-size:13px;text-align:center;line-height:30px}

  /* benefits */
  .benefits-title{left:753px;top:1769px;font-family:"Varela Round",Arial,sans-serif;font-size:29px;color:var(--orange)}
  .benefit-list{left:755px;top:1815px;list-style:none;font-size:13px;color:var(--grey)}
  .benefit-list li{height:30.3px;line-height:22px;display:flex;gap:10px}
  .benefit-list li::before{content:"";width:0;height:0;margin-top:7px;border-top:5px solid transparent;border-bottom:5px solid transparent;border-left:6px solid #b9b9b9}

  /* footer */
  .site-footer{left:0;top:2135px;width:1200px;height:71px;background:linear-gradient(180deg,#1a86c8,#0f6fae)}
  .footer-note{left:85px;top:2159px;font-size:12.5px;color:var(--white)}
  .social{left:1020px;top:2153px;display:flex;gap:6px}
  .social span{width:29px;height:29px;border-radius:50%;background:var(--white)}
</style>
</head>
<body>

<header class="abs site-header">
  <div class="abs brand" style="position:absolute">
    <span class="brand-mark"></span>
    <div>
      <div class="brand-name">TALKSIFT</div>
      <div class="brand-tag">BRING RESUMES TO LIFE</div>
    </div>
  </div>
  <nav>
    <a class="abs main-nav" style="left:647px">Benefits</a>
    <a class="abs main-nav" style="left:763px">Pricing</a>
    <a class="abs main-nav" style="left:868px">Login</a>
    <a class="abs main-nav" style="left:962px">Create Account</a>
  </nav>
</header>

<section class="abs hero"></section>
<h1 class="abs hero-kicker">Review candidate video’s</h1>
<div class="abs hero-title">anytime / anywhere</div>
<p class="abs hero-copy">Lorem ipsum dolor sit amet consectetuer adipiscing elit<br>Nam cursus Morbi ut mi Nullam enim leo egesta</p>
<a class="abs btn-read">READ MORE</a>
<div class="abs slider-dots"><span class="on"></span><span></span><span></span><span></span></div>
<div class="abs hero-visual" role="img" aria-label="Tablet showing a smiling professional woman emerging from a candidate video screen"></div>

<h2 class="abs welcome-title">Welcome to Our Website Mainpage</h2>
<p class="abs welcome-lead">Mauris vel lacus vitae felis vestibulum volutpat. Etiam est nunc, venenatis in, tristique eu, imperdiet ac, nisl.</p>
<p class="abs welcome-copy" style="top:700px">Cum sociis natoque penatibus et magnis dis parturient montes, nascetur ridiculus mus. In iaculis facilisis massa. Etiam eu urna. Sed porta. Suspendisse quam leo, molestie sed, luctus quis, feugiat in, pede. Fusce tellus. Sed metus augue, convallis et, vehicula ut</p>

<section class="abs steps" role="img" aria-label="Softly blurred bright office interior"></section>
<h2 class="abs steps-title">4 simple steps! Pre-screen your interviews</h2>
<div class="abs steps-sub">and hire who you need.</div>

<article class="abs step-card" style="left:94px">
  <svg class="step-icon" width="84" height="76" viewBox="0 0 84 76" aria-hidden="true">
    <rect x="4" y="40" width="16" height="34" rx="2" fill="#1a7dc0"/>
    <path d="M26 40 L44 18 L46 2 Q56 2 56 14 L54 32 L76 32 Q84 34 80 42 Q84 48 78 52 Q82 58 75 62 Q78 70 68 72 L26 72 Z" fill="#1a7dc0"/>
  </svg>
  <div class="step-head"><span class="step-num">1</span><span>Sign Up</span></div>
  <p class="step-copy">Morbi diam mauris viverra in gravida eu mattis in ante Morbi eget arcu Morbi</p>
</article>

<article class="abs step-card" style="left:349px">
  <svg class="step-icon" width="84" height="80" viewBox="0 0 84 80" aria-hidden="true">
    <rect x="4" y="30" width="76" height="46" fill="none" stroke="#1a7dc0" stroke-width="4"/>
    <path d="M4 30 L42 58 L80 30 M4 76 L32 52 M80 76 L52 52" fill="none" stroke="#1a7dc0" stroke-width="4"/>
    <path d="M42 2 L58 20 L48 20 L48 40 L36 40 L36 20 L26 20 Z" fill="#1a7dc0"/>
  </svg>
  <div class="step-head"><span class="step-num">2</span><span>Create Posting</span></div>
  <p class="step-copy">Morbi diam mauris viverra in gravida eu mattis in ante Morbi eget arcu Morbi</p>
</article>

<article class="abs step-card" style="left:603px">
  <svg class="step-icon" width="84" height="80" viewBox="0 0 84 80" aria-hidden="true">
    <circle cx="38" cy="20" r="18" fill="#1a7dc0"/>
    <path d="M4 78 Q4 44 38 42 Q64 44 70 60 L70 78 Z" fill="#1a7dc0"/>
    <circle cx="62" cy="58" r="17" fill="#ffffff"/>
    <circle cx="62" cy="58" r="14" fill="#1a7dc0"/>
    <rect x="59.5" y="55" width="5" height="12" fill="#ffffff"/>
    <circle cx="62" cy="50" r="3" fill="#ffffff"/>
  </svg>
  <div class="step-head"><span class="step-num">3</span><span>Invite Candidate</span></div>
  <p class="step-copy">Morbi diam mauris viverra in gravida eu mattis in ante Morbi eget arcu Morbi</p>
</article>

<article class="abs step-card" style="left:856px">
  <svg class="step-icon" width="88" height="70" viewBox="0 0 88 70" aria-hidden="true">
    <path d="M6 4 H82 Q86 4 86 8 V46 Q86 50 82 50 H52 L42 64 L34 50 H6 Q2 50 2 46 V8 Q2 4 6 4 Z" fill="none" stroke="#1a7dc0" stroke-width="4"/>
    <path d="M18 18 H70 M18 27 H70 M18 36 H70" stroke="#1a7dc0" stroke-width="3.5"/>
  </svg>
  <div class="step-head two-line"><span class="step-num">4</span><span class="lbl">Review you<br><span style="font-size:21px">Candidate</span></span></div>
  <p class="step-copy">Morbi diam mauris viverra in gravida eu mattis in ante Morbi eget arcu Morbi</p>
</article>

<section class="abs portal"></section>
<h2 class="abs portal-title">Talksift Admin Portal</h2>
<div class="abs portal-copy">
  <p>Pellentesque faucibus Ut accumsan ultricies elit Maecenas at justo id velit placerat molestie Donec dictum lectus non odio Cras a ante vitae enim iaculis aliquam Mauris nunc quam venenatis nec euismod sit amet egestas placerat est</p>
  <p>Pellentesque habitant morbi tristique senectus et netus et male-suada fames ac turpis egestas Cras id elit Integer quis urnaEtiam est nunc venenatis in tristique eu imperdiet ac nisl</p>
</div>
<div class="abs tablet-frame"></div>
<div class="abs tablet-home"></div>
<div class="abs tablet-screen" role="img" aria-label="Admin portal screen listing candidate interviews with ratings and reviewer comments"></div>

<h2 class="abs pricing-title">Pricing</h2>
<table class="abs price-table">
  <tr><td class="lbl">Interviews:</td><td class="num">05</td><td class="num">10</td><td class="num">25</td><td class="num">50</td></tr>
  <tr><td class="lbl">Price-Per-Interview:</td><td class="num">Free</td><td class="num">$15 Each</td><td class="num">$10 Each</td><td class="num">$5 Each</td></tr>
  <tr><td class="lbl">Total:</td><td class="num">FREE</td><td class="num">$150.00</td><td class="num">$250.00</td><td class="num">$500.00</td></tr>
</table>
<a class="abs btn-try">TRY IT FREE</a>

<h2 class="abs benefits-title">Our Benefits</h2>
<ul class="abs benefit-list">
  <li>Easy to use &amp; completely self-directed</li>
  <li>Reduce time and cost spent interviewing</li>
  <li>Customize interview questions &amp; your brand identity</li>
  <li>Interview candidates from anywhere in the world</li>
  <li>Review candidate videos anytime &amp; anywhere you want</li>
  <li>No need to evaluate candidates from memory</li>
  <li>Improve talent acquisition</li>
  <li>Invite anyone to review candidates</li>
  <li>Custom security</li>
</ul>

<footer class="abs site-footer"></footer>
<p class="abs footer-note">© 2014 Company Name &nbsp;All right reserved &nbsp;Term of Use</p>
<div class="abs social"><span></span><span></span><span></span></div>

</body>
</html>
```